Business card for medical clinic

I need an upmarket, modern medical/health business card for my clinic

Contact Information for Business Card

name, address, email, qr code

```html
<!DOCTYPE html>
<html lang="en">
<head>
<meta charset="utf-8">
<title>Meridian Care Group – Business Card</title>
<link rel="stylesheet" href="https://fonts.googleapis.com/css2?family=Montserrat:wght@400;500;700&display=swap">
<style>
  :root {
    --page-bg: #d9d4ce;
    --card-bg: #eeebe7;
    --card-edge: #f7f5f2;
    --brand-navy: #1c3f5e;
    --brand-teal: #1a8aa6;
    --name-ink: #1f5a7a;
    --body-ink: #3b3b3b;
  }
  * { box-sizing: border-box; margin: 0; padding: 0; }
  html, body {
    width: 1200px;
    height: 1047px;
    overflow: hidden;
    background: var(--page-bg);
    font-family: "Montserrat", sans-serif;
  }
  .business-card {
    position: absolute;
    left: 151px;
    top: 289px;
    width: 948px;
    height: 518px;
    border-radius: 26px;
    background: var(--card-bg);
    border: 2px solid var(--card-edge);
    box-shadow: 0 10px 30px rgba(0,0,0,0.12);
    overflow: hidden;
  }
  .brand-decoration {
    position: absolute;
    left: 428px;
    top: 20px;
    width: 520px;
    height: 478px;
    background: radial-gradient(ellipse at 55% 50%,
      rgba(26,138,166,0.28) 0%,
      rgba(28,63,94,0.18) 45%,
      rgba(238,235,231,0) 72%);
  }
  .brand {
    position: absolute;
    left: 40px;
    top: 52px;
    display: flex;
    align-items: center;
    gap: 14px;
  }
  .brand-dot {
    width: 40px;
    height: 40px;
    border-radius: 50%;
    background: var(--brand-navy);
  }
  .brand-name {
    font-weight: 500;
    font-size: 22px;
    letter-spacing: 0.5px;
    text-transform: uppercase;
    color: var(--brand-navy);
  }
  .accent-bar {
    position: absolute;
    left: 2px;
    top: 183px;
    width: 25px;
    height: 64px;
    background: linear-gradient(180deg, var(--brand-navy), var(--brand-teal));
  }
  .person-name {
    position: absolute;
    left: 40px;
    top: 177px;
    font-weight: 700;
    font-size: 38px;
    line-height: 1;
    letter-spacing: 0.5px;
    color: var(--name-ink);
  }
  .person-role {
    position: absolute;
    left: 37px;
    top: 216px;
    font-size: 26px;
    line-height: 31px;
    color: var(--body-ink);
  }
  .address {
    position: absolute;
    left: 37px;
    top: 286px;
    font-size: 26px;
    line-height: 37px;
    color: var(--body-ink);
  }
  .contact-list {
    position: absolute;
    left: 36px;
    top: 381px;
    list-style: none;
    font-size: 26px;
    line-height: 37px;
    color: var(--body-ink);
  }
  .contact-list li {
    display: flex;
    align-items: center;
    gap: 10px;
  }
  .contact-icon {
    width: 22px;
    height: 22px;
    fill: var(--body-ink);
    flex: none;
  }
</style>
</head>
<body>
  <div class="business-card">
    <div class="brand-decoration" role="img" aria-label="Large brand decoration in navy and teal tones"></div>

    <div class="brand">
      <span class="brand-dot"></span>
      <span class="brand-name">Meridian Care Group</span>
    </div>

    <span class="accent-bar"></span>
    <h1 class="person-name">DANIEL HART</h1>
    <p class="person-role">Managing Director</p>

    <p class="address">Your address, City<br>State, Zip 1234</p>

    <ul class="contact-list">
      <li>
        <svg class="contact-icon" viewBox="0 0 24 24" aria-hidden="true">
          <path d="M3 8c0-2 3-4 9-4s9 2 9 4v2h-5V8H8v2H3z"/>
          <path d="M6 11h12l2 9H4z"/>
        </svg>
        <span>123 456 789</span>
      </li>
      <li>
        <svg class="contact-icon" viewBox="0 0 24 24" aria-hidden="true">
          <path d="M2 9l10-6 10 6v12H2zM4 10v1l8 5 8-5v-1l-8 5z"/>
        </svg>
        <span>info@yourgmail.com</span>
      </li>
      <li>
        <svg class="contact-icon" viewBox="0 0 24 24" aria-hidden="true">
          <circle cx="12" cy="12" r="10"/>
          <path d="M2 12h20M12 2c3 3 3 17 0 20M12 2c-3 3-3 17 0 20" stroke="#eeebe7" stroke-width="1.5" fill="none"/>
        </svg>
        <span>www.yourwebsite.com</span>
      </li>
    </ul>
  </div>
</body>
</html>
```